Global (re)insurance broker needs a business card design

We need a classic business card for our company that is headquartered in SG, with offices in Malaysia and Dubai. We specialise in insurance and reinsurance broking and consultancy for our global clients.

```html
<!DOCTYPE html>
<html lang="en">
<head>
<meta charset="utf-8">
<title>Corvane Business Card</title>
<link rel="stylesheet" href="https://fonts.googleapis.com/css2?family=Open+Sans:wght@400;600;700&display=swap">
<style>
  :root {
    --page: #e6e6e9;
    --card-white: #f5f5f5;
    --card-black: #1d1d21;
    --emboss: #141417;
    --brand-blue: #24479b;
    --brand-green: #b8d4ab;
    --ink: #1a1a1a;
    --rule: #2a2a2a;
  }
  * { box-sizing: border-box; margin: 0; padding: 0; }
  html, body {
    width: 1200px; height: 780px; overflow: hidden;
    background: var(--page);
    font-family: "Open Sans", Arial, sans-serif;
  }
  .canvas {
    width: 1200px; height: 780px;
    display: flex; align-items: center; justify-content: center; gap: 40px;
  }
  .card {
    position: relative;
    width: 540px; height: 309px;
    box-shadow: 0 6px 18px rgba(0,0,0,0.18);
    overflow: hidden;
  }
  .card-front { background: var(--card-white); }
  .card-back { background: var(--card-black); display: flex; align-items: center; justify-content: center; }

  .wordmark {
    position: absolute; top: 52px; left: 222px;
    font-weight: 700; font-size: 62px; letter-spacing: 1px;
    color: var(--brand-blue); line-height: 1;
  }
  .wordmark-back {
    font-weight: 700; font-size: 74px; letter-spacing: 1px;
    color: var(--emboss); line-height: 1;
  }

  .identity { position: absolute; top: 152px; left: 38px; }
  .person-name { font-weight: 600; font-size: 30px; line-height: 1.05; color: var(--brand-blue); }
  .person-name .surname { color: var(--brand-green); }
  .person-title { font-size: 13.5px; color: var(--ink); margin-top: 2px; }

  .divider {
    position: absolute; top: 170px; left: 244px;
    width: 1px; height: 70px; background: var(--rule);
  }

  .contacts { position: absolute; top: 172px; left: 262px; list-style: none; }
  .contacts li {
    display: flex; align-items: center; gap: 8px;
    font-size: 14px; color: var(--ink); line-height: 22px;
  }
  .contacts svg { width: 12px; height: 12px; flex: none; }

  .address-band {
    position: absolute; left: 0; right: 0; bottom: 0; height: 30px;
    background: var(--brand-blue); color: #fff;
    font-size: 13.5px; display: flex; align-items: center; padding-left: 30px;
  }
</style>
</head>
<body>
<main class="canvas">
  <section class="card card-front">
    <div class="wordmark">CORVANE</div>
    <div class="identity">
      <h1 class="person-name">Maren <span class="surname">Loh</span></h1>
      <p class="person-title">Chief Operating Officer</p>
    </div>
    <div class="divider"></div>
    <ul class="contacts">
      <li>
        <svg viewBox="0 0 12 12"><rect x="2.5" y="0.5" width="7" height="11" rx="1.2" fill="none" stroke="#b8d4ab"/></svg>
        +65 9000 4821
      </li>
      <li>
        <svg viewBox="0 0 12 12"><circle cx="6" cy="6" r="5.5" fill="#24479b"/><path d="M0.8 6h10.4M6 0.5c-2.5 3-2.5 8 0 11M6 0.5c2.5 3 2.5 8 0 11" stroke="#fff" stroke-width="0.7" fill="none"/></svg>
        www.corvane.com
      </li>
      <li>
        <svg viewBox="0 0 12 12"><rect x="0.5" y="2" width="11" height="8" rx="1" fill="#b8d4ab"/><path d="M0.8 2.5L6 6.5l5.2-4" stroke="#fff" stroke-width="0.9" fill="none"/></svg>
        maren@corvane.com
      </li>
    </ul>
    <div class="address-band">22 Harbour Lane, Meridian Tower #08-04, Singapore 049512</div>
  </section>

  <section class="card card-back">
    <div class="wordmark-back">CORVANE</div>
  </section>
</main>
</body>
</html>
```